Young, dynamic furniture company needs a new business card design

We require a new business card design for our modern furniture company which supplies furniture and appliances to the property and development market.
Oakridge Interiors has become one of the leading furniture & appliance suppliers to the property market withing London. With over 10 years experience, we have increased our business to supply not only private landlords and managing agents, but also property developers, housing associations and local councils.
We offer not only a complete range of furniture which includes beds, wardrobes, dining sets and sofas, but also a high quality, full delivery and assembly service to help you with all our furnishing needs.

Target Market(s)

Private landlords, estate agents, letting agents, property management companies

Industry/Entity Type

Business

Contact Information for Business Card

Name,
Title,
Address,
Mobile,
Telephone,
Fax, Website, email address

Font styles to use
Sans Serif

Colors
3176b5
0555a3
85abd2
cfdeed

Requirements
Must have
• All the above information for each of our staff, along with our logo

```html
<!DOCTYPE html>
<html lang="en">
<head>
<meta charset="utf-8">
<title>Oakridge Interiors – Business Card</title>
<link href="https://fonts.googleapis.com/css2?family=Roboto:wght@400;500&display=swap" rel="stylesheet">
<style>
  :root {
    --page-bg: #e9edf2;
    --brand-blue: #3176b5;
    --brand-navy: #0555a3;
    --panel-navy: #1d3f8c;
    --brand-light: #85abd2;
    --brand-pale: #cfdeed;
    --ink: #2a2a2a;
    --white: #ffffff;
  }
  * { margin: 0; padding: 0; box-sizing: border-box; }
  html, body { width: 1200px; height: 950px; overflow: hidden; }
  body {
    background: var(--page-bg);
    font-family: "Roboto", Arial, sans-serif;
    position: relative;
  }
  .card {
    position: absolute;
    left: 250px;
    width: 700px;
    height: 400px;
    overflow: hidden;
    box-shadow: 0 6px 18px rgba(0,0,0,0.15);
  }

  /* Front side */
  .card-front {
    top: 55px;
    background: var(--brand-blue);
    color: var(--white);
    text-align: center;
  }
  .front-brand {
    position: absolute;
    top: 120px;
    left: 0; right: 0;
    display: flex;
    flex-direction: column;
    align-items: center;
  }
  .brand-line { display: flex; align-items: center; gap: 14px; white-space: nowrap; }
  .brand-dot {
    width: 22px; height: 22px;
    flex: none;
    background: var(--white);
  }
  .brand-name {
    font-size: 34px;
    font-weight: 500;
    letter-spacing: 1px;
    text-transform: uppercase;
  }
  .brand-tagline {
    margin-top: 8px;
    font-size: 13px;
    letter-spacing: 1.5px;
    text-transform: uppercase;
    white-space: nowrap;
  }
  .front-web {
    position: absolute;
    bottom: 70px;
    left: 0; right: 0;
    font-size: 16px;
    letter-spacing: 6px;
  }

  /* Back side */
  .card-back {
    top: 495px;
    background: var(--white);
  }
  .back-shapes { position: absolute; inset: 0; }
  .back-brand {
    position: absolute;
    left: 40px;
    top: 165px;
    width: 300px;
    color: var(--ink);
  }
  .back-brand .brand-line { gap: 12px; }
  .back-brand .brand-dot { width: 19px; height: 19px; background: var(--brand-navy); }
  .back-brand .brand-name { font-size: 23px; letter-spacing: 0.5px; }
  .back-brand .brand-tagline { font-size: 10px; letter-spacing: 1.2px; margin-top: 6px; padding-left: 31px; }

  .contact {
    position: absolute;
    right: 32px;
    top: 38px;
    color: var(--white);
    text-align: right;
  }
  .contact-name {
    font-size: 22px;
    font-weight: 500;
    letter-spacing: 1px;
    text-transform: uppercase;
  }
  .contact-title {
    font-size: 14px;
    letter-spacing: 1px;
    text-transform: uppercase;
    margin-top: 3px;
  }
  .contact-list { list-style: none; margin-top: 48px; }
  .contact-list li {
    display: flex;
    justify-content: flex-end;
    align-items: center;
    gap: 10px;
    font-size: 15px;
    line-height: 24px;
    white-space: nowrap;
  }
  .contact-list .address { display: block; padding-right: 28px; }
  .icon { width: 16px; height: 16px; flex: none; fill: var(--white); }
</style>
</head>
<body>

<section class="card card-front" aria-label="Card front">
  <div class="front-brand">
    <div class="brand-line">
      <span class="brand-dot"></span>
      <span class="brand-name">Oakridge Interiors</span>
    </div>
    <div class="brand-tagline">Trade Furniture Solutions</div>
  </div>
  <div class="front-web">www.oakridgeinteriors.com</div>
</section>

<section class="card card-back" aria-label="Card back">
  <svg class="back-shapes" width="700" height="400" viewBox="0 0 700 400">
    <polygon points="378,0 388,0 378,400 366,400" fill="var(--brand-blue)"/>
    <polygon points="392,0 700,0 700,400 382,400" fill="var(--panel-navy)"/>
  </svg>

  <div class="back-brand">
    <div class="brand-line">
      <span class="brand-dot"></span>
      <span class="brand-name">Oakridge Interiors</span>
    </div>
    <div class="brand-tagline">Trade Furniture Solutions</div>
  </div>

  <div class="contact">
    <div class="contact-name">Daniel Marsh</div>
    <div class="contact-title">President</div>
    <ul class="contact-list">
      <li class="address">2417 Harborview Lane<br>Maple Grove, NY 11020</li>
      <li>512 6408 3917
        <svg class="icon" viewBox="0 0 16 16"><path d="M3 1h3l1 4-2 1c1 2 3 4 5 5l1-2 4 1v3c0 1-1 2-2 2C7 15 1 9 1 3c0-1 1-2 2-2z"/></svg></li>
      <li>840 2196 7734
        <svg class="icon" viewBox="0 0 16 16"><path d="M4 0h8a1 1 0 0 1 1 1v14a1 1 0 0 1-1 1H4a1 1 0 0 1-1-1V1a1 1 0 0 1 1-1zm1 2v10h6V2zm3 11a1 1 0 1 0 0 2 1 1 0 0 0 0-2z"/></svg></li>
      <li>836 5172 4409
        <svg class="icon" viewBox="0 0 16 16"><path d="M4 1h7v4H4zM1 6h14v7h-3v2H4v-2H1zm4 5v3h6v-3z"/></svg></li>
      <li>daniel@oakridge.com
        <svg class="icon" viewBox="0 0 16 16"><path d="M1 3h14v10H1zm1 1v1l6 4 6-4V4z"/></svg></li>
      <li>www.oakridgeinteriors.com
        <svg class="icon" viewBox="0 0 16 16"><path d="M8 1a7 7 0 1 0 0 14A7 7 0 0 0 8 1zm0 1.5c1 1 1.6 2.8 1.7 4.7H6.3C6.4 5.3 7 3.5 8 2.5zM6.3 8.8h3.4c-.1 1.9-.7 3.700-1.700 4.700-1-1-1.600-2.800-1.700-4.700zM2.6 7.2a5.5 5.5 0 0 1 2.5-4c-.4 1.1-.7 2.5-.8 4zm0 1.6h1.7c.1 1.5.4 2.9.8 4a5.5 5.5 0 0 1-2.5-4zm10.8 0a5.5 5.5 0 0 1-2.5 4c.4-1.1.7-2.5.8-4zm0-1.6h-1.7c-.1-1.5-.4-2.9-.8-4a5.5 5.5 0 0 1 2.5 4z"/></svg></li>
    </ul>
  </div>
</section>

</body>
</html>
```